Baby Organic Coconut Body Lotion

Meadow Hush Naturals is developing a line of Organic and Natural skin care products for babies and toddlers, although our skin care can also be used by adults too. These products include a body lotion, shampoo & body wash, powder, hair cream, massage body oil, bath soak, baby balm, Bar Soap, gift box and many more.
This will be an ever expanding line so the list will go on and on. We are looking forward for an eye catching designs. I attached some of our current label designs and product images. Also, we have different Baby organic body lotion and Baby organic shampoo & body wash with different fruit flavours. Coconut lotion will share the same design with the shampoo & body wash. I would like you to start with the coconut design. I have uploaded plastic bottles with different colourful caps. The bottle with the white cap is for the coconut design. the bottle with the red cap is for the strawberry design. the bottle with the orange cap is for the orange design. the bottle with the yellow cap is for the pineapple design. the bottle with the green cap is for the apple design. Bear in my mind that my baby organic skin care are made with different fruit flavours.
Target Market(s)
My target market are for mothers that wants to buy there baby and toddler skin care products.
Industry/Entity Type
Baby
Look and feel

```html
<!DOCTYPE html>
<html lang="en">
<head>
<meta charset="utf-8">
<title>Meadow Hush Naturals – Baby Organic Body Lotion Labels</title>
<link href="https://fonts.googleapis.com/css2?family=Economica:wght@400;700&display=swap" rel="stylesheet">
<style>
  :root {
    --page-bg: #ecebea;
    --label-bg: #ffffff;
    --small-text: #ffffff;
    --apple: #a6bf5c;
    --apple-band: linear-gradient(90deg, #b8cf74, #93b04a);
    --apple-photo: linear-gradient(160deg, #c9dc8a 0%, #8fbf3e 45%, #5f9a2a 100%);
    --pineapple: #c6b74a;
    --pineapple-band: linear-gradient(90deg, #cfc06a, #9d8b2e);
    --pineapple-photo: linear-gradient(160deg, #f6e04a 0%, #e3c23a 40%, #b68a3a 70%, #6f9a5a 100%);
    --strawberry: #d26f78;
    --strawberry-band: linear-gradient(90deg, #d7757c, #8c1f27);
    --strawberry-photo: linear-gradient(160deg, #f07a7e 0%, #d9333c 45%, #a81f2a 80%, #5d8a3a 100%);
    --orange: #f0ad23;
    --orange-band: linear-gradient(90deg, #f6c23a, #eea51c);
    --orange-photo: linear-gradient(160deg, #6fae3a 0%, #f6b21c 35%, #f39a10 75%, #f7c84a 100%);
    --coconut: #8c8789;
    --coconut-band: linear-gradient(90deg, #a7a2a3, #8a8586);
    --coconut-photo: linear-gradient(160deg, #f4f4f2 0%, #d9dbd8 35%, #8a6a4a 65%, #5a3e26 100%);
  }
  * { box-sizing: border-box; margin: 0; padding: 0; }
  html, body { width: 1200px; height: 1200px; overflow: hidden; }
  body {
    background: var(--page-bg);
    font-family: "Economica", "Arial Narrow", sans-serif;
    display: flex;
    align-items: center;
    justify-content: center;
  }
  .label-row { display: flex; gap: 20px; }
  .label {
    width: 212px;
    height: 440px;
    background: var(--label-bg);
    display: flex;
    flex-direction: column;
    box-shadow: 0 2px 8px rgba(0,0,0,0.12);
  }
  .brand {
    height: 128px;
    display: flex;
    align-items: center;
    justify-content: center;
    gap: 8px;
    padding: 0 12px;
  }
  .brand-dot { width: 12px; height: 12px; border-radius: 50%; background: var(--accent); flex: none; }
  .brand-name {
    color: var(--accent);
    font-weight: 700;
    font-size: 25px;
    line-height: 1.05;
    text-align: left;
  }
  .product-name {
    color: var(--accent);
    font-size: 25px;
    line-height: 1.3;
    text-align: center;
    height: 80px;
    display: flex;
    flex-direction: column;
    justify-content: center;
  }
  .ingredient-band {
    background: var(--band);
    color: var(--small-text);
    font-size: 17px;
    text-align: center;
    padding: 6px 0;
  }
  .tested {
    color: var(--accent);
    font-size: 12px;
    font-weight: 700;
    text-align: center;
    padding: 8px 0 6px;
  }
  .fruit-photo {
    flex: 1;
    background: var(--photo);
    position: relative;
  }
  .photo-footer {
    position: absolute;
    left: 0; right: 0; bottom: 0;
    display: flex;
    justify-content: space-between;
    padding: 0 12px 10px;
    color: var(--small-text);
    font-size: 16px;
    font-weight: 700;
    text-shadow: 0 1px 2px rgba(0,0,0,0.35);
  }
  .apple { --accent: var(--apple); --band: var(--apple-band); --photo: var(--apple-photo); }
  .pineapple { --accent: var(--pineapple); --band: var(--pineapple-band); --photo: var(--pineapple-photo); }
  .strawberry { --accent: var(--strawberry); --band: var(--strawberry-band); --photo: var(--strawberry-photo); }
  .orange { --accent: var(--orange); --band: var(--orange-band); --photo: var(--orange-photo); }
  .coconut { --accent: var(--coconut); --band: var(--coconut-band); --photo: var(--coconut-photo); }
</style>
</head>
<body>
  <main class="label-row">
    <article class="label apple">
      <div class="brand"><span class="brand-dot"></span><span class="brand-name">Meadow Hush<br>Naturals</span></div>
      <div class="product-name"><span>Baby Organic</span><span>Apple Body Lotion</span></div>
      <div class="ingredient-band">With Shea &amp; Cocoa Butter</div>
      <div class="tested">Dermatologically tested</div>
      <div class="fruit-photo" role="img" aria-label="Photo of green apples with a halved apple and leaves">
        <div class="photo-footer"><span>80% organic</span><span>125ml e</span></div>
      </div>
    </article>
    <article class="label pineapple">
      <div class="brand"><span class="brand-dot"></span><span class="brand-name">Meadow Hush<br>Naturals</span></div>
      <div class="product-name"><span>Baby Organic</span><span>Pineapple Body Lotion</span></div>
      <div class="ingredient-band">With Shea &amp; Cocoa Butter</div>
      <div class="tested">Dermatologically tested</div>
      <div class="fruit-photo" role="img" aria-label="Photo of a cut pineapple with slices">
        <div class="photo-footer"><span>80% organic</span><span>125ml e</span></div>
      </div>
    </article>
    <article class="label strawberry">
      <div class="brand"><span class="brand-dot"></span><span class="brand-name">Meadow Hush<br>Naturals</span></div>
      <div class="product-name"><span>Baby Organic</span><span>Strawberry Body Lotion</span></div>
      <div class="ingredient-band">With Shea &amp; Cocoa Butter</div>
      <div class="tested">Dermatologically tested</div>
      <div class="fruit-photo" role="img" aria-label="Photo of fresh red strawberries">
        <div class="photo-footer"><span>80% organic</span><span>125ml e</span></div>
      </div>
    </article>
    <article class="label orange">
      <div class="brand"><span class="brand-dot"></span><span class="brand-name">Meadow Hush<br>Naturals</span></div>
      <div class="product-name"><span>Baby Organic</span><span>Orange Body Lotion</span></div>
      <div class="ingredient-band">With Shea &amp; Cocoa Butter</div>
      <div class="tested">Dermatologically tested</div>
      <div class="fruit-photo" role="img" aria-label="Photo of a whole orange with leaf and a halved orange">
        <div class="photo-footer"><span>80% organic</span><span>125ml e</span></div>
      </div>
    </article>
    <article class="label coconut">
      <div class="brand"><span class="brand-dot"></span><span class="brand-name">Meadow Hush<br>Naturals</span></div>
      <div class="product-name"><span>Baby Organic</span><span>Coconut Body Lotion</span></div>
      <div class="ingredient-band">With Shea &amp; Cocoa Butter</div>
      <div class="tested">Dermatologically tested</div>
      <div class="fruit-photo" role="img" aria-label="Photo of a whole coconut and a cracked coconut half">
        <div class="photo-footer"><span>80% organic</span><span>125ml e</span></div>
      </div>
    </article>
  </main>
</body>
</html>
```